Personal training and nutrition business needs business card design

We need a business card that outlays our services and invites potential customers to join our team and take the first step to a healthier and more enjoyable life. We cater for any level of fitness and specialize in weight loss and conditioning, strength training, muscle gain and strength endurance. Whether you are just starting off or need some help getting to the next level of your journey we are here to get the job done.
We specialize in one on one or one on two personal training sessions and each program will be custom made to suit individual fitness goals of our clients

```html
<!DOCTYPE html>
<html lang="en">
<head>
<meta charset="utf-8">
<title>Stride &amp; Pulse – Business Card</title>
<link rel="stylesheet" href="https://fonts.googleapis.com/css2?family=Roboto:wght@400;500;700;900&family=Oswald:wght@500&family=Exo+2:ital,wght@1,800&display=swap">
<style>
  :root {
    --backdrop: #2c2c2c;
    --ink: #141414;
    --text: #2a2a2a;
    --purple: #7b4aa3;
    --violet: #5c3b95;
    --orchid: #a2559f;
    --tagline: #9b55a0;
    --white: #ffffff;
  }
  * { box-sizing: border-box; margin: 0; padding: 0; }
  html, body { width: 1200px; height: 1138px; overflow: hidden; }
  body {
    background: var(--backdrop);
    font-family: "Roboto", sans-serif;
    position: relative;
  }
  .card {
    position: absolute;
    width: 621px;
    height: 375px;
    background: linear-gradient(135deg, #f3f3f3 0%, #e4e4e4 100%);
    border-radius: 16px;
    overflow: hidden;
  }
  .card--front { left: 274px; top: 186px; }
  .card--back  { left: 275px; top: 608px; }

  /* Front */
  .brand {
    position: absolute;
    left: 0; right: 0;
    top: 205px;
    display: flex;
    align-items: center;
    justify-content: center;
    gap: 14px;
  }
  .brand__dot {
    width: 36px; height: 36px;
    border-radius: 50%;
    background: var(--purple);
  }
  .brand__name {
    font-weight: 900;
    font-size: 38px;
    letter-spacing: 1px;
    color: var(--ink);
    line-height: 1;
  }
  .tagline {
    font-family: "Oswald", sans-serif;
    font-weight: 500;
    color: var(--tagline);
    letter-spacing: 1.2px;
    text-transform: uppercase;
  }
  .card--front .tagline {
    position: absolute;
    top: 252px; left: 0; right: 0;
    text-align: center;
    font-size: 13px;
  }
  .site-line {
    position: absolute;
    top: 318px; left: 0; right: 0;
    display: flex;
    align-items: center;
    justify-content: center;
    gap: 18px;
    font-size: 15px;
    color: var(--ink);
  }
  .site-line__rule {
    width: 70px; height: 2px;
    background: var(--ink);
  }
  .accent { color: var(--purple); }
  .accent--deep { color: var(--violet); }
  .base-strip {
    position: absolute;
    left: 0; right: 0; bottom: 0;
    height: 10px;
    background: linear-gradient(90deg, var(--orchid), var(--violet));
  }

  /* Back */
  .header-band {
    position: absolute;
    left: 0; top: 0;
    width: 621px; height: 110px;
  }
  .person {
    position: absolute;
    left: 33px; top: 26px;
    color: var(--white);
  }
  .person__name {
    font-family: "Exo 2", sans-serif;
    font-style: italic;
    font-weight: 800;
    font-size: 25px;
    letter-spacing: 0.5px;
  }
  .person__role {
    font-size: 15px;
    margin-top: 2px;
  }
  .back-brand {
    position: absolute;
    left: 290px; top: 124px;
    display: flex;
    align-items: center;
    gap: 16px;
  }
  .back-brand__dot {
    width: 62px; height: 62px;
    border-radius: 50%;
    background: var(--purple);
  }
  .back-brand__name {
    font-weight: 900;
    font-size: 32px;
    line-height: 1.02;
    color: var(--ink);
    letter-spacing: 1px;
  }
  .back-brand .tagline {
    font-size: 8px;
    margin-top: 6px;
    letter-spacing: 0.8px;
  }
  .contacts {
    position: absolute;
    left: 30px; top: 270px;
    list-style: none;
    font-size: 15.5px;
    color: var(--text);
  }
  .contacts li {
    display: flex;
    align-items: center;
    gap: 14px;
    height: 24.5px;
  }
  .contacts svg { width: 15px; height: 15px; fill: var(--purple); }
  .address {
    position: absolute;
    right: 30px; top: 296px;
    text-align: right;
    font-size: 15.5px;
    line-height: 24px;
    color: var(--text);
    font-style: normal;
  }
</style>
</head>
<body>

<section class="card card--front">
  <div class="brand">
    <span class="brand__dot"></span>
    <span class="brand__name">STRIDE &amp; PULSE</span>
  </div>
  <p class="tagline">Personal Training.&nbsp; Nutrition. Motivation</p>
  <div class="site-line">
    <span class="site-line__rule"></span>
    <span>www.<span class="accent">strideand</span><span class="accent--deep">pulse</span>.com</span>
    <span class="site-line__rule"></span>
  </div>
  <div class="base-strip"></div>
</section>

<section class="card card--back">
  <svg class="header-band" viewBox="0 0 621 110" role="img" aria-label="Purple gradient header wave">
    <defs>
      <linearGradient id="band" x1="0" y1="0" x2="1" y2="0">
        <stop offset="0" stop-color="#a2559f"/>
        <stop offset="1" stop-color="#5c3b95"/>
      </linearGradient>
    </defs>
    <path d="M0 0 H621 V70 C470 30 330 110 0 100 Z" fill="url(#band)"/>
  </svg>

  <div class="person">
    <h1 class="person__name">DAN MERROW</h1>
    <p class="person__role">Personal Trainer</p>
  </div>

  <div class="back-brand">
    <span class="back-brand__dot"></span>
    <div>
      <div class="back-brand__name">STRIDE<br>&amp; PULSE</div>
      <p class="tagline">Personal Training.&nbsp; Nutrition. Motivation</p>
    </div>
  </div>

  <ul class="contacts">
    <li>
      <svg viewBox="0 0 24 24"><path d="M6.6 10.8a15 15 0 0 0 6.6 6.6l2.2-2.2a1 1 0 0 1 1-.25 11.4 11.4 0 0 0 3.6.57 1 1 0 0 1 1 1V20a1 1 0 0 1-1 1A17 17 0 0 1 3 4a1 1 0 0 1 1-1h3.5a1 1 0 0 1 1 1c0 1.25.2 2.45.57 3.57a1 1 0 0 1-.25 1z"/></svg>
      <span>+12 (555) 014-2290</span>
    </li>
    <li>
      <svg viewBox="0 0 24 24"><path d="M2 5h20v14H2z M4 7v.5l8 5 8-5V7l-8 5z" fill-rule="evenodd"/></svg>
      <span>dan@strideandpulse.com</span>
    </li>
    <li>
      <svg viewBox="0 0 24 24"><path d="M12 2a10 10 0 1 0 0 20 10 10 0 0 0 0-20zm6.9 6h-3a15 15 0 0 0-1.3-3.9A8 8 0 0 1 18.9 8zM12 4c.9 1.2 1.6 2.5 2 4h-4c.4-1.5 1.1-2.8 2-4zM4.3 14a8 8 0 0 1 0-4h3.4a16 16 0 0 0 0 4zm.8 2h3a15 15 0 0 0 1.3 3.9A8 8 0 0 1 5.1 16zm3-8h-3a8 8 0 0 1 4.3-3.9A15 15 0 0 0 8.1 8zM12 20c-.9-1.2-1.6-2.5-2-4h4c-.4 1.5-1.1 2.8-2 4zm2.3-6H9.7a14 14 0 0 1 0-4h4.6a14 14 0 0 1 0 4zm.3 5.9a15 15 0 0 0 1.3-3.9h3a8 8 0 0 1-4.3 3.9zm1.7-5.9a16 16 0 0 0 0-4h3.4a8 8 0 0 1 0 4z"/></svg>
      <span>www.<span class="accent--deep">strideand</span><span class="accent">pulse</span>.com</span>
    </li>
  </ul>

  <address class="address">
    812 Cedar Ridge Lane<br>
    Lakeview Texas 75000
  </address>
</section>

</body>
</html>
```